Business card design

I am open to ideas. I was thinking of a vertical design, turning the name 90 degrees and placing it on the left edge, then some clipped portion of the fabulous tree with contact info on the bottom -- special emphasis on Web address:WhimBeads.comFor All Your Beading Needs121 E. Cotati AveCotati, CA 94931(707) 664-8343

```html
<!DOCTYPE html>
<html lang="en">
<head>
<meta charset="utf-8">
<title>Fern &amp; Glass Co. — Business Card</title>
<link href="https://fonts.googleapis.com/css2?family=Playfair+Display:wght@400;700&display=swap" rel="stylesheet">
<style>
  :root {
    --bg: #e9e6e1;
    --card: #ffffff;
    --ink: #1c1c1c;
    --muted: #3a3a3a;
    --violet: #6a3b9c;
    --green: #2f9a3c;
    --yellow: #f0c419;
    --orange: #f08a1c;
    --red: #e0312b;
  }
  * { box-sizing: border-box; margin: 0; padding: 0; }
  html, body { width: 1200px; height: 780px; overflow: hidden; }
  body {
    background: var(--bg);
    font-family: "Playfair Display", Georgia, serif;
    color: var(--ink);
    position: relative;
  }
  .card {
    position: absolute;
    top: 80px;
    width: 354px;
    height: 620px;
    background: var(--card);
    box-shadow: 0 6px 22px rgba(0,0,0,.18);
    overflow: hidden;
  }
  .card--front { left: 210px; }
  .card--back { left: 636px; }
  .card__band { position: absolute; left: 0; width: 100%; }
  .card--front .card__band { bottom: 0; height: 130px; }
  .card--back .card__band { top: 0; height: 130px; }

  .brand {
    position: absolute;
    top: 150px; left: 0; width: 100%;
    display: flex; align-items: center; justify-content: center; gap: 12px;
  }
  .brand__mark {
    width: 22px; height: 22px; border-radius: 50%;
    background: var(--green);
  }
  .brand__name {
    font-size: 30px; font-weight: 400; color: var(--ink);
  }
  .person { position: absolute; top: 232px; width: 100%; text-align: center; }
  .person__name { font-size: 30px; font-weight: 700; letter-spacing: .5px; }
  .person__title { font-size: 17px; color: var(--muted); margin-top: -2px; }

  .contact {
    position: absolute; left: 0; width: 100%;
    text-align: center;
  }
  .contact__rule { display: block; margin: 0 auto; }
  .contact__text { font-size: 19px; line-height: 1.3; margin-top: 8px; }
  .contact--phone { top: 316px; }
  .contact--address { top: 390px; }

  .web {
    position: absolute; bottom: 26px; width: 100%;
    text-align: center;
    font-size: 20px; font-weight: 700; letter-spacing: 5px;
    color: var(--ink);
  }
  .card--back .web {
    top: 30px; bottom: auto;
    transform: rotate(180deg);
  }
  .back-brand {
    position: absolute; top: 360px; width: 100%;
    display: flex; align-items: center; justify-content: center; gap: 12px;
  }
</style>
</head>
<body>

<svg width="0" height="0" style="position:absolute" aria-hidden="true">
  <defs>
    <linearGradient id="rainbow" x1="0" y1="0" x2="1" y2="0">
      <stop offset="0" stop-color="#6a3b9c"/>
      <stop offset=".3" stop-color="#2f9a3c"/>
      <stop offset=".6" stop-color="#f0c419"/>
      <stop offset=".8" stop-color="#f08a1c"/>
      <stop offset="1" stop-color="#e0312b"/>
    </linearGradient>
    <linearGradient id="rule-left" x1="0" y1="0" x2="1" y2="0">
      <stop offset="0" stop-color="#6a3b9c" stop-opacity=".2"/>
      <stop offset="1" stop-color="#2f9a3c"/>
    </linearGradient>
    <linearGradient id="rule-right" x1="0" y1="0" x2="1" y2="0">
      <stop offset="0" stop-color="#f0c419"/>
      <stop offset="1" stop-color="#e0312b" stop-opacity=".2"/>
    </linearGradient>
  </defs>
</svg>

<section class="card card--front">
  <div class="brand">
    <span class="brand__mark"></span>
    <span class="brand__name">Fern &amp; Glass Co.</span>
  </div>

  <div class="person">
    <div class="person__name">Owen Hale</div>
    <div class="person__title">Manager</div>
  </div>

  <div class="contact contact--phone">
    <svg class="contact__rule" width="300" height="30" viewBox="0 0 300 30">
      <line x1="20" y1="15" x2="132" y2="15" stroke="url(#rule-left)" stroke-width="2"/>
      <line x1="168" y1="15" x2="280" y2="15" stroke="url(#rule-right)" stroke-width="2"/>
      <circle cx="150" cy="15" r="14" fill="url(#rainbow)"/>
      <circle cx="150" cy="15" r="9" fill="#fff"/>
      <path d="M146 10 q-2 5 2 9 q2 2 5 1 l1-2 -2-2 -2 1 q-2-2-2-4 l1-1 -1-3 z" fill="#2f9a3c"/>
    </svg>
    <p class="contact__text">(707) 555-0192</p>
  </div>

  <div class="contact contact--address">
    <svg class="contact__rule" width="300" height="30" viewBox="0 0 300 30">
      <line x1="20" y1="15" x2="132" y2="15" stroke="url(#rule-left)" stroke-width="2"/>
      <line x1="168" y1="15" x2="280" y2="15" stroke="url(#rule-right)" stroke-width="2"/>
      <circle cx="150" cy="15" r="14" fill="url(#rainbow)"/>
      <circle cx="150" cy="15" r="9" fill="#fff"/>
      <path d="M150 21 q-5-6 -5-9 a5 5 0 0 1 10 0 q0 3 -5 9 z" fill="#2f9a3c"/>
      <circle cx="150" cy="12" r="1.8" fill="#fff"/>
    </svg>
    <p class="contact__text">348 W. Brindle Ave, Larkfield<br>CA 94999</p>
  </div>

  <svg class="card__band" viewBox="0 0 354 130" preserveAspectRatio="none" aria-hidden="true">
    <path d="M0 0 Q150 70 354 55 L354 130 L0 130 Z" fill="url(#rainbow)"/>
  </svg>
  <p class="web">FernGlassco.com</p>
</section>

<section class="card card--back">
  <svg class="card__band" viewBox="0 0 354 130" preserveAspectRatio="none" aria-hidden="true">
    <path d="M0 130 Q204 60 354 75 L354 0 L0 0 Z" fill="url(#rainbow)" transform="rotate(180 177 65)"/>
  </svg>
  <p class="web">FernGlassco.com</p>
  <div class="back-brand">
    <span class="brand__mark"></span>
    <span class="brand__name">Fern &amp; Glass Co.</span>
  </div>
</section>

</body>
</html>
```